Constant Contact email marketing template

I need engaging customizable templates that can be used in multiple fundraising campaigns.

I included a school bus project that we used in a previous campaign. This campaign, however, is a $25 for $25 promotion. Consumers make a $25 contribution for the school or charity and receive back a $25 e-gift card to be used at area restaurants.

Important! This is a completely generic piece, capable of being used in schools, churches, or other civic organizations.

The 5 part example is NOT what I am looking for. I included it to suggest the concept. I am looking forward to viewing YOUR designs,

Target Market(s)

schools, leagues, nonprofit organizations

Font styles to use
Sans Serif

Colors

Designer to choose colors to be used in the design.

Requirements
Must have
• Must clearly present itself as a fundraising tool for schools, leagues and Nonprofit organizations.
• Must have 2 clickable buttons that allow member to click

```html
<!DOCTYPE html>
<html lang="en">
<head>
<meta charset="utf-8">
<title>Greatest Fundraiser Ever – Donate $25, Get $25</title>
<link rel="stylesheet" href="https://fonts.googleapis.com/css2?family=Kaushan+Script&family=Oswald:wght@300;400;500&family=Open+Sans:wght@400;600;700;800&family=Open+Sans+Condensed:wght@300&display=swap">
<style>
  :root {
    --white: #ffffff;
    --ink: #111111;
    --black-band: #151515;
    --orange: #e8671f;
    --orange-light: #f39a2e;
    --orange-deep: #d4481a;
    --red: #c3262c;
    --red-dark: #9e1b22;
    --crimson: #c8202f;
    --gold: #e6ad48;
    --gold-dark: #c98c24;
    --silver: #d9d9d9;
    --photo-a: #c9b7a6;
    --photo-b: #e8ddd2;
  }
  * { box-sizing: border-box; margin: 0; padding: 0; }
  html, body { width: 1200px; height: 2356px; overflow: hidden; background: var(--white); }
  .canvas { position: relative; width: 1200px; height: 2356px; overflow: hidden; background: var(--white); font-family: "Open Sans", sans-serif; color: var(--ink); }
  .backdrop { position: absolute; inset: 0; }

  .headline { position: absolute; right: 48px; top: 24px; text-align: right; }
  .headline .script { font-family: "Kaushan Script", cursive; color: var(--white); display: block; }
  .headline .small { font-size: 44px; line-height: 1; margin-right: 40px; }
  .headline .caps { font-family: "Oswald", sans-serif; font-weight: 400; color: var(--gold); font-size: 42px; letter-spacing: 12px; display: block; line-height: 1.15; margin-right: -8px; }
  .headline .big { font-size: 84px; line-height: 1; }

  .offer-frame { position: absolute; left: 282px; top: 612px; width: 566px; height: 442px; border: 3px solid var(--gold); border-radius: 14px; }
  .card { position: absolute; background: linear-gradient(180deg, #ffffff, #eeeeee); box-shadow: 0 14px 22px rgba(0,0,0,.25); overflow: hidden; }
  .card .price { position: absolute; top: 0; right: 0; bottom: 0; background: linear-gradient(135deg, #d23a3a, var(--red-dark)); color: var(--white); font-family: "Oswald", sans-serif; font-weight: 500; display: flex; align-items: center; justify-content: center; clip-path: polygon(12% 0, 100% 0, 100% 100%, 0 100%); }
  .card .price sup { font-size: .42em; margin-top: -.7em; }
  .card-donate { left: 128px; top: 560px; width: 600px; height: 246px; transform: rotate(-7deg); }
  .card-donate .price { width: 230px; font-size: 132px; padding-left: 30px; }
  .card-donate .word { position: absolute; left: 40px; top: 108px; font-family: "Kaushan Script", cursive; color: var(--crimson); font-size: 92px; }
  .and-you-get { position: absolute; left: 318px; top: 760px; font-family: "Kaushan Script", cursive; color: var(--gold); font-size: 108px; transform: rotate(-6deg); text-shadow: 0 4px 6px rgba(0,0,0,.15); white-space: nowrap; }
  .card-gift { left: 498px; top: 890px; width: 620px; height: 250px; transform: rotate(-8deg); }
  .card-gift .price { width: 290px; font-size: 132px; padding-left: 40px; }
  .gift-label { position: absolute; left: 30px; top: 80px; width: 270px; height: 120px; border: 4px solid var(--ink); text-align: center; }
  .gift-label .script { font-family: "Kaushan Script", cursive; color: var(--crimson); font-size: 70px; line-height: 1.35; }
  .gift-label .tag { position: absolute; left: 50%; bottom: -18px; transform: translateX(-50%); background: #f2f2f2; padding: 0 12px; font-family: "Oswald", sans-serif; font-size: 26px; letter-spacing: 5px; color: var(--crimson); }

  .button { position: absolute; display: flex; align-items: center; justify-content: center; border-radius: 50%; text-decoration: none; background: radial-gradient(circle at 30% 25%, #ffffff, var(--silver) 60%, #a9a9a9); box-shadow: 0 10px 24px rgba(0,0,0,.28); }
  .button .face { border-radius: 50%; display: flex; flex-direction: column; align-items: center; justify-content: center; text-align: center; font-family: "Oswald", sans-serif; font-weight: 300; text-transform: uppercase; }
  .button-donate { left: 66px; top: 1208px; width: 368px; height: 368px; }
  .button-donate .face { width: 310px; height: 310px; background: radial-gradient(circle at 35% 30%, #e2492f, var(--red) 55%, #8f1418); color: var(--white); }
  .button-donate .cta-small { font-size: 38px; }
  .button-donate .cta-big { font-size: 76px; line-height: 1.12; }
  .button-behalf { left: 64px; top: 1848px; width: 352px; height: 352px; }
  .button-behalf .face { width: 296px; height: 296px; background: radial-gradient(circle at 35% 30%, #f7c85a, var(--gold-dark) 70%, #a8701a); color: #5b3c0f; }
  .button-behalf .cta-small { font-size: 36px; margin-bottom: 6px; }
  .button-behalf .cta-body { font-size: 40px; line-height: 1.22; }

  .pitch { position: absolute; left: 480px; top: 1282px; width: 680px; }
  .pitch h2 { font-weight: 700; font-size: 48px; line-height: 1.2; color: var(--ink); white-space: nowrap; }
  .pitch .quote { margin-top: 26px; font-size: 22px; letter-spacing: 2px; line-height: 1.3; text-transform: uppercase; font-weight: 600; }

  .benefits { position: absolute; left: 186px; top: 1648px; list-style: none; }
  .benefits li { display: flex; align-items: center; gap: 14px; font-size: 31px; font-weight: 700; color: var(--crimson); line-height: 52px; }
  .benefits svg { width: 36px; height: 36px; flex: none; }

  .behalf-copy { position: absolute; left: 450px; top: 1868px; width: 590px; }
  .behalf-copy h3 { font-weight: 800; font-size: 62px; color: var(--crimson); line-height: 1.1; }
  .behalf-copy p { margin-top: 24px; font-size: 18.5px; line-height: 1.32; text-align: justify; }

  .contact { position: absolute; right: 38px; top: 2168px; list-style: none; text-align: right; }
  .contact li { display: flex; justify-content: flex-end; align-items: center; gap: 14px; color: var(--white); font-size: 18px; line-height: 60px; text-transform: uppercase; }
  .contact .icon { width: 42px; height: 42px; border: 3px solid var(--white); border-radius: 50%; display: flex; align-items: center; justify-content: center; }
  .contact svg { width: 22px; height: 22px; fill: var(--white); }
</style>
</head>
<body>
<main class="canvas">
  <svg class="backdrop" width="1200" height="2356" viewBox="0 0 1200 2356" aria-hidden="true">
    <defs>
      <linearGradient id="photoTone" x1="0" y1="0" x2="1" y2="1">
        <stop offset="0" stop-color="var(--photo-b)"/>
        <stop offset="1" stop-color="var(--photo-a)"/>
      </linearGradient>
      <linearGradient id="orangeSweep" x1="0" y1="0" x2="1" y2="0">
        <stop offset="0" stop-color="#f6a63a"/>
        <stop offset="1" stop-color="#e2531c"/>
      </linearGradient>
      <linearGradient id="footerSweep" x1="0" y1="0" x2="1" y2="0">
        <stop offset="0" stop-color="#e24a1d"/>
        <stop offset="1" stop-color="#f2992e"/>
      </linearGradient>
    </defs>
    <path d="M760 0 H1200 V330 C1000 360 860 400 700 440 C900 300 900 110 760 0 Z" fill="var(--black-band)"/>
    <path d="M1200 330 V470 C880 470 480 540 0 760 V700 C320 520 720 430 1200 330 Z" fill="url(#orangeSweep)"/>
    <path d="M1060 470 C760 500 420 560 40 760 C380 600 720 520 1060 470 Z" fill="var(--orange-deep)"/>
    <path d="M0 2356 H1200 V1980 C1080 2170 740 2300 0 2334 Z" fill="url(#footerSweep)"/>
    <path d="M1200 1950 C1100 2130 760 2270 180 2316 C760 2250 1080 2120 1200 1900 Z" fill="var(--orange-light)"/>
  </svg>

  <svg class="crowd-photo" role="img" aria-label="Photo of a cheering group of people celebrating" width="1200" height="760" viewBox="0 0 1200 760" style="position:absolute;left:0;top:0">
    <path d="M0 0 H760 C880 120 860 300 690 390 C480 470 250 520 0 700 Z" fill="url(#photoTone)"/>
  </svg>

  <header class="headline">
    <span class="script small">greatest</span>
    <span class="caps">FUNDRAISER</span>
    <span class="script big">ever!</span>
  </header>

  <div class="offer-frame"></div>
  <div class="card card-donate">
    <span class="word">donate</span>
    <span class="price"><sup>$</sup>25</span>
  </div>
  <div class="and-you-get">and you get</div>
  <div class="card card-gift">
    <div class="gift-label"><span class="script">e-Gift</span><span class="tag">CARD</span></div>
    <span class="price"><sup>$</sup>25</span>
  </div>

  <a class="button button-donate" href="#donate">
    <span class="face"><span class="cta-small">Clik here</span><span class="cta-big">Donate<br>now!</span></span>
  </a>

  <section class="pitch">
    <h2>Simply donate $25 and<br>we give you $25 back in<br>e-Gift Cards for<br>restaurants in your area!</h2>
    <p class="quote">"Sed ut perspiciatis unde omnis iste<br>natus error sit voluptatem ac</p>
  </section>

  <ul class="benefits">
    <li><svg viewBox="0 0 24 24"><path d="M2 12 L9 20 L22 3 L9 14 Z" fill="var(--crimson)"/></svg>More than 500,000 deals available every day</li>
    <li><svg viewBox="0 0 24 24"><path d="M2 12 L9 20 L22 3 L9 14 Z" fill="var(--crimson)"/></svg>Local independent neughborhood restaurants</li>
    <li><svg viewBox="0 0 24 24"><path d="M2 12 L9 20 L22 3 L9 14 Z" fill="var(--crimson)"/></svg>Always available. Never expire.</li>
  </ul>

  <a class="button button-behalf" href="#donate-behalf">
    <span class="face"><span class="cta-small">Clik here</span><span class="cta-body">Donate on behalf<br>of a loved one<br>or friend</span></span>
  </a>

  <section class="behalf-copy">
    <h3>$25 for $25</h3>
    <p>"Sed ut perspiciatis unde omnis iste natus error sit voluptatem accusantium doloremque laudantium, totam rem aperiam, eaque ipsa quae ab illo inventore veritatis et quasi architecto beatae vitae dicta sunt explicabo. Nemo enim ipsam voluptatem quia voluptas sit aspernatur aut odit aut fugit, sed quia consequuntur magni dolores eos qui ratione voluptatem sequi nesciunt.</p>
  </section>

  <ul class="contact">
    <li>Addres<span class="icon"><svg viewBox="0 0 24 24"><path d="M12 3 L2 12 H5 V21 H10 V15 H14 V21 H19 V12 H22 Z"/></svg></span></li>
    <li>+01 555 0142 736<span class="icon"><svg viewBox="0 0 24 24"><path d="M6.6 10.8c1.4 2.8 3.8 5.1 6.6 6.6l2.2-2.2c.3-.3.7-.4 1-.2 1.1.4 2.3.6 3.6.6.6 0 1 .4 1 1V20c0 .6-.4 1-1 1C10.6 21 3 13.4 3 4c0-.6.4-1 1-1h3.5c.6 0 1 .4 1 1 0 1.3.2 2.5.6 3.6.1.3 0 .7-.2 1z"/></svg></span></li>
    <li>hello@givebackclub.org<span class="icon"><svg viewBox="0 0 24 24"><path d="M3 6 H21 V18 H3 Z M3 6 L12 13 L21 6" fill="none" stroke="#fff" stroke-width="2"/></svg></span></li>
  </ul>
</main>
</body>
</html>
```